Counseling Practice Business Card

I need a professional looking business card incorporating my new logo that was just completed. Card needs to incorporate my name and title, description of my specialty, my address, my phone number, my fax number, my email and my website URL. I need to be able to choose design on/with different paper colors and textures.
I do not have a lot of business card ideas so I am open to anything but I want bold,sharp, clear card without additional designs other than my logo (see attached file info). I am open to different color backgrounds or paper colors including black. I do not like traditional brackets around area codes in phone number or dashes between numbers in phone number. Am open to other ways of presenting including periods between numbers as appropriate. I do not know enough to know what I like yet but I want card to coordinate and work together with my logo. My practice emphasizes natural mental health interventions so any use of color (with background paper color or the blue and green in my logo) that elicits nature is nice. In addition to black, any natural brown or wood looking background might be desirable also. Most of the offerings so far look very similar and boring.

Target Market(s)

Potential therapy clients and other professionals

Contact Information for Business Card

Card information:
Gerald M. Whitcombe, Ph.D.
Licensed Clinical Psychologist
Integrative Health Coach
4812 Marlowe Ridge Blvd SE
Suite 310
Alder Springs, GA 30084
(770) 415-2983 phone
(770) 581-4096 fax
drgeraldwhitcombe@quillmarsh.net
brightfernwellness.net

Font styles to use
Serif
Sans Serif
Other font styles liked:
• anything that you think looks crisp, clear and easily readable

Requirements
Must have
• Any color used should coordinate with my logo design (see attached files).
• Card should be printed horizontally so top and bottom are longest sides of rectangle.
• Background color or paper color should complement and highlight logo. Do not like a white background. black, grey, brown or any color my logo would blend well with.
Nice to have
• I would like designer to utilize color to highlight letters/name or phone-fax-web symbols.
• Bottom edge of card could be highlighted if appropriate to an idea.
Should not have
• I would NOT want the card to have a pure white background at all.
• No clear cards.
• Cards should be oriented with long sides on bottom and top, NOT sides. DO NOT LIKE THIS THIN TALL ORIENTATION.

```html
<!DOCTYPE html>
<html lang="en">
<head>
<meta charset="utf-8">
<title>Brightfern Counseling — Business Card</title>
<link href="https://fonts.googleapis.com/css2?family=Open+Sans:wght@700&family=Crimson+Text:wght@400;600&display=swap" rel="stylesheet">
<style>
  :root {
    --backdrop: #b9bdbe;
    --card: #1d1d1e;
    --brand-blue: #2a7cc7;
    --brand-green: #1f7a3c;
    --ink-light: #eef0ef;
    --shadow: rgba(0, 0, 0, 0.28);
  }
  * { margin: 0; padding: 0; box-sizing: border-box; }
  html, body {
    width: 1200px;
    height: 824px;
    overflow: hidden;
    background: var(--backdrop);
  }
  .canvas {
    position: relative;
    width: 1200px;
    height: 824px;
    display: flex;
    align-items: center;
    justify-content: center;
    gap: 44px;
  }
  .card {
    position: relative;
    width: 520px;
    height: 297px;
    background: var(--card);
    border-radius: 3px;
    box-shadow: 0 10px 28px var(--shadow);
    overflow: hidden;
  }

  /* Back: contact details */
  .identity {
    position: absolute;
    left: 58px;
    top: 70px;
    text-align: right;
  }
  .identity__name {
    font-family: "Open Sans", Arial, sans-serif;
    font-weight: 700;
    font-size: 17px;
    color: var(--brand-blue);
    letter-spacing: -0.2px;
  }
  .identity__title {
    font-family: "Crimson Text", Georgia, serif;
    font-size: 14.5px;
    line-height: 1.15;
    color: var(--brand-green);
  }
  .contact {
    position: absolute;
    left: 300px;
    top: 92px;
    list-style: none;
    font-family: "Crimson Text", Georgia, serif;
    font-size: 13.5px;
    line-height: 1.3;
    color: var(--ink-light);
  }
  .address {
    position: absolute;
    left: 58px;
    bottom: 44px;
    font-family: "Crimson Text", Georgia, serif;
    font-size: 13.5px;
    color: var(--ink-light);
    font-style: normal;
  }

  /* Front: brand */
  .card--front {
    display: flex;
    align-items: center;
    justify-content: center;
  }
  .brand {
    display: flex;
    align-items: center;
    gap: 14px;
  }
  .brand__dot {
    width: 22px;
    height: 22px;
    border-radius: 50%;
    background: var(--brand-blue);
  }
  .brand__name {
    font-family: "Crimson Text", Georgia, serif;
    font-weight: 600;
    font-size: 36px;
    color: var(--brand-blue);
    letter-spacing: 0.5px;
  }
</style>
</head>
<body>
  <main class="canvas">
    <section class="card card--back" aria-label="Business card, contact side">
      <div class="identity">
        <h1 class="identity__name">Gerald M. Whitcombe, Ph.D.</h1>
        <p class="identity__title">Licensed Clinical Psychologist</p>
        <p class="identity__title">Integrative Health Coach</p>
      </div>
      <ul class="contact">
        <li>(770) 415-2983 phone</li>
        <li>(770) 581-4096 fax</li>
        <li>drgeraldwhitcombe@quillmarsh.net</li>
        <li>brightfernwellness.net</li>
      </ul>
      <address class="address">4812 Marlowe Ridge Blvd SE, Suite 310, Alder Springs, GA 30084</address>
    </section>

    <section class="card card--front" aria-label="Business card, brand side">
      <div class="brand">
        <span class="brand__dot"></span>
        <span class="brand__name">Brightfern Counseling</span>
      </div>
    </section>
  </main>
</body>
</html>
```